Ferncrest Roam Wording For Logo & Business card

I have the logo, I just need the "Ferncrest Roam" wording to go with it, and a business card design. The only thing on the business card is the website info. We provide nature connection experiences, and bolster these efforts through writing and host a platform for community around it.

I also have an idea of what it could look like (sketch), though I'm really not sure how it would come out. I am open to the best design and happy to consider original artwork. You can see what the site is about at FerncrestRoam.example.

Contact Information for Business Card

The only thing on the business card is the website info and the design. I will put other messaging on the back.

Website lettering (FerncrestRoam.example) in Montserrat

Logo Text

Ferncrest Roam (letters optional)

Font styles to use
Other font styles liked:
• montserrat

```html
<!DOCTYPE html>
<html lang="en">
<head>
<meta charset="utf-8">
<title>Ferncrest Roam – Business Card</title>
<link rel="stylesheet" href="https://fonts.googleapis.com/css2?family=Montserrat:wght@300;400;500&display=swap">
<style>
  :root {
    --backdrop: #2a2a2a;
    --card-white: #ffffff;
    --night: #140d26;
    --ink: #1a1530;
    --ember: #f08a1e;
    --muted: #8c8c8c;
  }
  * { box-sizing: border-box; margin: 0; padding: 0; }
  html, body {
    width: 1200px; height: 583px; overflow: hidden;
    background: var(--backdrop);
    font-family: "Montserrat", sans-serif;
  }
  .stage { position: relative; width: 1200px; height: 583px; }

  .card {
    position: absolute; top: 154px;
    width: 481px; height: 275px;
    border-radius: 32px; overflow: hidden;
    background: var(--card-white);
  }
  .card--front { left: 94px; }
  .card--back { left: 627px; }

  /* Front */
  .front-mark {
    position: absolute; left: 200px; top: 52px;
    width: 82px; height: 82px; border-radius: 50%;
    background: var(--night);
  }
  .front-name {
    position: absolute; left: 0; right: 0; top: 146px;
    text-align: center;
    font-weight: 300; font-size: 26px; letter-spacing: 0.06em;
    text-transform: uppercase; color: var(--ink);
  }
  .front-band {
    position: absolute; left: 0; right: 0; top: 220px; bottom: 0;
    background: var(--night);
  }
  .front-web {
    position: absolute; left: 70px; width: 340px; top: 212px; height: 20px;
    background: var(--card-white);
    border-radius: 0 0 8px 8px;
    text-align: center;
    font-size: 13px; font-weight: 400; line-height: 20px;
    letter-spacing: 0.32em; color: var(--ink);
  }
  .front-web .accent { color: var(--ember); }

  /* Back */
  .back-band {
    position: absolute; left: 0; right: 0; top: 0; height: 98px;
    background: var(--night);
  }
  .back-tab {
    position: absolute; left: 170px; top: 81px; width: 282px; height: 30px;
    background: var(--card-white);
    border-radius: 10px 10px 0 0;
  }
  .back-ring {
    position: absolute; left: 55px; top: 35px;
    width: 124px; height: 124px; border-radius: 50%;
    background: var(--card-white);
  }
  .back-mark {
    position: absolute; left: 62px; top: 42px;
    width: 110px; height: 110px; border-radius: 50%;
    background: var(--night);
  }
  .back-name {
    position: absolute; left: 180px; top: 82px;
    font-weight: 300; font-size: 26px; letter-spacing: 0.06em;
    text-transform: uppercase; color: var(--ink); white-space: nowrap;
  }
  .person {
    position: absolute; left: 190px; top: 143px;
  }
  .person__name {
    font-size: 16px; font-weight: 400; letter-spacing: 0.02em;
    text-transform: uppercase; color: var(--ink); line-height: 18px;
  }
  .person__role {
    font-size: 13px; font-weight: 400; color: var(--muted); line-height: 17px;
  }
  .contact {
    position: absolute; left: 190px; top: 188px;
    list-style: none;
  }
  .contact li {
    display: flex; align-items: center; gap: 5px;
    font-size: 13px; font-weight: 400; color: var(--muted);
    line-height: 19px; white-space: nowrap;
  }
  .contact svg { width: 10px; height: 10px; flex: none; }
</style>
</head>
<body>
<main class="stage">

  <section class="card card--front">
    <div class="front-mark"></div>
    <h1 class="front-name">Ferncrest Roam</h1>
    <div class="front-band"></div>
    <p class="front-web">www.<span class="accent">ferncrestroam</span>.example</p>
  </section>

  <section class="card card--back">
    <div class="back-band"></div>
    <div class="back-tab"></div>
    <div class="back-ring"></div>
    <div class="back-mark"></div>
    <h2 class="back-name">Ferncrest Roam</h2>

    <div class="person">
      <p class="person__name">Mara Lindqvist</p>
      <p class="person__role">Manager</p>
    </div>

    <ul class="contact">
      <li>
        <svg viewBox="0 0 10 10" aria-hidden="true"><circle cx="5" cy="5" r="5" fill="var(--ember)"/><path d="M3.2 2.6l1 1-0.6 0.7c0.4 0.8 1 1.4 1.8 1.8l0.7-0.6 1 1-0.8 0.9c-2 -0.4-3.6-2-4-4z" fill="#fff"/></svg>
        555-014-2290
      </li>
      <li>
        <svg viewBox="0 0 10 10" aria-hidden="true"><circle cx="5" cy="5" r="5" fill="var(--ember)"/><rect x="2.6" y="3.3" width="4.8" height="3.4" fill="#fff"/><path d="M2.6 3.3L5 5.2 7.4 3.3" stroke="var(--ember)" stroke-width="0.6" fill="none"/></svg>
        info@ferncrestroam.example
      </li>
      <li>
        <svg viewBox="0 0 10 10" aria-hidden="true"><circle cx="5" cy="5" r="5" fill="var(--ember)"/><path d="M5 2.2L7.6 4.6V7.6H2.4V4.6z" fill="#fff"/></svg>
        12 Alder Lane, Pinecove, box 40217
      </li>
    </ul>
  </section>

</main>
</body>
</html>
```